New Business Card Design for Manufacturing

We are an engineering/manufacturing company that offers Advanced machining/assembly/engineering services, as well as innovative products for the heavy duty engine cooling markets.

We are looking to get a new business card designed that is clean and modern looking, but still fits the wide range of technical/skilled work we do.

- We hope to use this design as the base for other design work in new Presentations, web, and print work.

Industry/Entity Type

Engineering

Contact Information for Business Card

Our preferred color of blue is (RGB) 22/71/159 but can vary slightly from that color. Our content will be our Logo and full company name (Vantrell Forge Works, Inc.), company address, name, job title, phone number with extension, cell number, fax number, website, and email address on the cards.
We'd like the full company name next to the logo, but we are open to other interpretations of that layout.
Preferably, we would like the back side to be clean with just our logo, and the front to contain all of the contact information.

Colors
2f74b4
0355a3
85abd2

Requirements
Must have
• - Logo, company name, needed content - We are open to interpretation beyond that.
• - Standard size business card.
• - Horizontal orientation.
• - Enough space for lengthy names / job titles (for example, a job title could read "Directory of Human Resources" or "V.P. of Governmental Affairs"). We need this to look clean, whether the title be short (CEO) or long (as described above).

```html
<!DOCTYPE html>
<html lang="en">
<head>
<meta charset="utf-8">
<title>Vantrell Forge Works – Business Card</title>
<link rel="stylesheet" href="https://fonts.googleapis.com/css2?family=Fira+Sans:wght@400;500;700;800&family=Open+Sans:wght@400&display=swap">
<style>
  :root {
    --brand-blue: #0f4d93;
    --brand-blue-deep: #0a3f7c;
    --steel-grey: #7a8087;
    --ink: #3a3d42;
    --card-white: #f7f7f6;
    --card-black: #0b0c0d;
    --backdrop: #e6e6e4;
  }
  * { box-sizing: border-box; margin: 0; padding: 0; }
  html, body {
    width: 1200px; height: 576px; overflow: hidden;
    background: var(--backdrop);
  }
  .canvas { position: relative; width: 1200px; height: 576px; }

  .card {
    position: absolute; top: 138px;
    width: 484px; height: 294px;
    border-radius: 14px; overflow: hidden;
  }

  /* back side */
  .card-back { left: 82px; background: var(--card-black); }
  .back-mark {
    position: absolute; inset: 0;
    display: flex; align-items: center; justify-content: center; gap: 14px;
  }
  .back-mark .mark-square { width: 22px; height: 22px; background: var(--brand-blue); }
  .back-mark .mark-name {
    font-family: "Fira Sans", sans-serif; font-weight: 800;
    font-size: 58px; color: #ffffff; letter-spacing: 0.5px;
  }

  /* front side */
  .card-front { left: 602px; width: 480px; background: var(--card-white); }
  .edge-tab {
    position: absolute; left: -12px; top: 50px;
    width: 24px; height: 24px; border-radius: 50%;
    background: var(--brand-blue);
  }
  .front-mark {
    position: absolute; right: 24px; top: 28px;
    font-family: "Fira Sans", sans-serif; font-weight: 800;
    font-size: 40px; color: var(--brand-blue); line-height: 1;
  }
  .holder-name {
    position: absolute; left: 22px; top: 43px;
    font-family: "Fira Sans", sans-serif; font-weight: 500;
    font-size: 20px; color: var(--brand-blue);
  }
  .holder-title {
    position: absolute; left: 22px; top: 68px;
    font-family: "Open Sans", sans-serif; font-size: 11.5px; color: var(--ink);
  }
  .company-name {
    position: absolute; left: 22px; top: 120px;
    font-family: "Fira Sans", sans-serif; font-weight: 500;
    font-size: 15px; color: var(--brand-blue);
  }
  .contact-list {
    position: absolute; left: 22px; top: 146px; list-style: none;
    font-family: "Open Sans", sans-serif; font-size: 12.5px; color: var(--ink);
  }
  .contact-list li {
    display: flex; align-items: center; height: 17.4px;
  }
  .contact-list svg { width: 11px; height: 11px; margin-right: 9px; fill: var(--brand-blue-deep); }
  .contact-list .accent { color: var(--brand-blue); }

  .wave { position: absolute; left: 0; top: 0; width: 480px; height: 294px; }
  .address {
    position: absolute; right: 22px; top: 232px; text-align: right;
    font-family: "Open Sans", sans-serif; font-size: 12.5px; line-height: 17px;
    color: #ffffff;
  }
</style>
</head>
<body>
<main class="canvas">

  <section class="card card-back" aria-label="Card back">
    <div class="back-mark">
      <span class="mark-square"></span>
      <span class="mark-name">Vantrell</span>
    </div>
  </section>

  <section class="card card-front" aria-label="Card front">
    <svg class="wave" viewBox="0 0 480 294" aria-hidden="true">
      <path d="M0 236 C70 272 170 276 270 238 C350 208 420 194 480 188 V198 C420 204 352 218 282 246 C180 286 80 284 0 250 Z" fill="var(--steel-grey)"/>
      <path d="M0 272 C110 312 210 262 300 228 C370 202 430 198 480 196 V294 H0 Z" fill="var(--brand-blue)"/>
    </svg>

    <span class="edge-tab"></span>
    <div class="front-mark">Vantrell</div>

    <h1 class="holder-name">Marlon Reyes Castell</h1>
    <p class="holder-title">Managing Director</p>

    <h2 class="company-name">Vantrell Forge Works, Inc.</h2>
    <ul class="contact-list">
      <li><svg viewBox="0 0 12 12"><path d="M1 3 C1 2 2 1.5 6 1.5 S11 2 11 3 V4.5 H8.5 V3.5 H3.5 V4.5 H1Z M2.5 5.5 H9.5 L10.5 10.5 H1.5Z"/></svg>248-555-0170 (VFW)</li>
      <li><svg viewBox="0 0 12 12"><path d="M3.5 0.5 H8.5 A1 1 0 0 1 9.5 1.5 V10.5 A1 1 0 0 1 8.5 11.5 H3.5 A1 1 0 0 1 2.5 10.5 V1.5 A1 1 0 0 1 3.5 0.5Z M4 2 V9 H8 V2Z"/></svg>248-555-0193</li>
      <li><svg viewBox="0 0 12 12"><path d="M3 0.5 H9 V4 H3Z M1 4.5 H11 V9 H9 V7 H3 V9 H1Z M3.5 7.5 H8.5 V11.5 H3.5Z"/></svg>248-555-0148</li>
      <li><svg viewBox="0 0 12 12"><path d="M0.5 2.5 H11.5 V3.2 L6 7 L0.5 3.2Z M0.5 4.4 L6 8.2 L11.5 4.4 V9.5 H0.5Z"/></svg>m.castell@vantrellforge.com</li>
      <li><svg viewBox="0 0 12 12"><path d="M6 0.5 A5.5 5.5 0 1 0 6.01 0.5Z M6 1.8 C7 3 7.4 4.5 7.4 6 S7 9 6 10.2 C5 9 4.6 7.5 4.6 6 S5 3 6 1.8Z M1.8 5.4 H10.2 V6.6 H1.8Z" fill-rule="evenodd"/></svg>www.<span class="accent">vantrellforge</span>.com</li>
    </ul>

    <address class="address">518 Millrace Rd., Suite 4<br>Dunmore Falls, US 48213</address>
  </section>

</main>
</body>
</html>
```